SkyvornQ Business Cards and Stationary Design

Need a design for our business cards and stationary. I want to carry on the theme of the logo. I want the business cards to have a design on the back. I would like the business cards and the stationary to carry the same theme, design scheme, and branding

Target Market(s)

Airlines and Maintenance Facilities

Industry/Entity Type

Aviation

Contact Information for Business Card

Name
Position Title
Address: 4827 Trellis Hollow Road, Fort Pierce, Florida, 34951
Office Number
Mobile Number
Email
Website

Font styles to use
Serif
Sans Serif

Colors

Designer to choose colors to be used in the design.

```html
<!DOCTYPE html>
<html lang="en">
<head>
<meta charset="utf-8">
<title>SkyvornQ Business Card</title>
<link rel="stylesheet" href="https://fonts.googleapis.com/css2?family=Michroma&family=PT+Sans:wght@400;700&display=swap">
<style>
  :root {
    --navy: #13294f;
    --blue: #1d74c4;
    --text-grey: #4a4f57;
    --rule: #c9ccd1;
    --card: #ffffff;
    --backdrop: #e9eaec;
  }
  * { box-sizing: border-box; margin: 0; padding: 0; }
  html, body { width: 1200px; height: 872px; overflow: hidden; }
  body {
    background: var(--backdrop);
    font-family: "PT Sans", sans-serif;
    position: relative;
  }
  .card {
    position: absolute;
    top: 288px;
    width: 520px;
    height: 297px;
    background: var(--card);
    box-shadow: 0 6px 20px rgba(0,0,0,.12);
  }
  .card--brand { left: 60px; }
  .card--contact { left: 620px; }

  /* brand side */
  .brand-lockup {
    position: absolute;
    left: 0; right: 0; top: 92px;
    display: flex; align-items: center; justify-content: center; gap: 16px;
  }
  .brand-dot {
    width: 46px; height: 46px; border-radius: 50%;
    border: 6px solid var(--blue);
  }
  .wordmark {
    font-family: "Michroma", sans-serif;
    color: var(--navy);
    letter-spacing: 4px;
  }
  .brand-lockup .wordmark { font-size: 34px; }
  .brand-url {
    position: absolute; left: 0; right: 0; top: 168px;
    text-align: center;
    font-size: 15px; letter-spacing: 4px; color: #333;
  }

  /* contact side */
  .card--contact .wordmark {
    position: absolute; left: 0; right: 0; top: 62px;
    text-align: center; font-size: 38px; letter-spacing: 5px;
  }
  .details {
    position: absolute; top: 150px; left: 40px; right: 30px;
    display: flex;
  }
  .person {
    width: 230px; padding-right: 16px; text-align: right;
  }
  .person-name { font-weight: 700; font-size: 17px; color: var(--navy); }
  .person-title { font-size: 15px; color: var(--text-grey); letter-spacing: .5px; }
  .person-address {
    margin-top: 8px; font-size: 12.5px; color: #222; line-height: 1.3;
    display: flex; justify-content: flex-end; gap: 5px;
  }
  .divider { width: 1px; background: var(--rule); height: 100px; }
  .contact-list {
    list-style: none; padding-left: 16px;
    font-size: 13.5px; color: #222; line-height: 1.55;
  }
  .contact-list li { display: flex; align-items: center; gap: 6px; }
  .icon { width: 13px; height: 13px; flex: none; }
</style>
</head>
<body>
  <section class="card card--brand">
    <div class="brand-lockup">
      <span class="brand-dot"></span>
      <span class="wordmark">SKYVORNQ</span>
    </div>
    <p class="brand-url">www.skyvornq.com</p>
  </section>

  <section class="card card--contact">
    <h1 class="wordmark">SKYVORNQ</h1>
    <div class="details">
      <div class="person">
        <p class="person-name">DARREN WHITCOMBE</p>
        <p class="person-title">PRESIDENT</p>
        <p class="person-address">
          <svg class="icon" viewBox="0 0 14 14" aria-hidden="true"><circle cx="7" cy="7" r="6" fill="none" stroke="#13294f" stroke-width="1.2"/><path d="M7 3.5a2 2 0 0 1 2 2c0 1.6-2 4-2 4s-2-2.4-2-4a2 2 0 0 1 2-2z" fill="#1d74c4"/></svg>
          <span>Street Name, City Name<br>Zipcode-012345</span>
        </p>
      </div>
      <div class="divider"></div>
      <ul class="contact-list">
        <li><svg class="icon" viewBox="0 0 14 14" aria-hidden="true"><circle cx="7" cy="7" r="6" fill="none" stroke="#13294f" stroke-width="1.2"/><path d="M4.5 4l1.3-.4.8 1.6-.8.6a4 4 0 0 0 2.4 2.4l.6-.8 1.6.8-.4 1.3C7.5 9.5 4.5 6.5 4.5 4z" fill="#1d74c4"/></svg>012-555-0148</li>
        <li><svg class="icon" viewBox="0 0 14 14" aria-hidden="true"><circle cx="7" cy="7" r="6" fill="none" stroke="#13294f" stroke-width="1.2"/><rect x="5" y="3.5" width="4" height="7" rx=".8" fill="none" stroke="#1d74c4" stroke-width="1.1"/></svg>012-555-0148</li>
        <li><svg class="icon" viewBox="0 0 14 14" aria-hidden="true"><circle cx="7" cy="7" r="6" fill="none" stroke="#13294f" stroke-width="1.2"/><rect x="3.8" y="4.8" width="6.4" height="4.4" fill="none" stroke="#1d74c4" stroke-width="1"/><path d="M3.8 4.8L7 7.3l3.2-2.5" fill="none" stroke="#1d74c4" stroke-width="1"/></svg>info@skyvornq.com</li>
        <li><svg class="icon" viewBox="0 0 14 14" aria-hidden="true"><circle cx="7" cy="7" r="6" fill="none" stroke="#13294f" stroke-width="1.2"/><circle cx="7" cy="7" r="3.5" fill="none" stroke="#1d74c4" stroke-width="1"/><path d="M3.5 7h7M7 3.5v7" stroke="#1d74c4" stroke-width="1"/></svg>www.skyvornq.com</li>
      </ul>
    </div>
  </section>
</body>
</html>
```